Need a website setup for our new removalist business.
Our business is called Harbour Lane Removals and would like a website setup.
We don’t have a website, logo or design as of yet. Our truck is blue so something possibly that works and can incorporate the blue.

```html
<!DOCTYPE html>
<html lang="en">
<head>
<meta charset="utf-8">
<title>Harbour Lane Removals</title>
<link href="https://fonts.googleapis.com/css2?family=Poppins:wght@400;500;600;700&family=Merriweather:wght@700;900&family=Arimo:wght@400;600&display=swap" rel="stylesheet">
<style>
:root{
  --blue:#2f6b8f;
  --blue-dark:#245a7a;
  --blue-band:#346f93;
  --ink:#111;
  --text:#333;
  --white:#fff;
  --muted:#e9eef2;
  --gold:#f5a623;
  --black:#000;
}
*{box-sizing:border-box;margin:0;padding:0}
html,body{width:1200px;height:3955px;overflow:hidden}
body{position:relative;background:var(--white);font-family:"Arimo",Arial,sans-serif;color:var(--text)}
.abs{position:absolute}
.fill{display:block}
/* header */
.site-header{position:absolute;left:0;top:0;width:1200px;height:88px;background:var(--white);z-index:3}
.brand{position:absolute;left:110px;top:20px;display:flex;align-items:center;gap:10px;font-family:"Poppins",sans-serif;font-weight:600;font-size:17px;color:var(--ink)}
.brand .dot{width:30px;height:30px;border-radius:50%;background:var(--blue)}
.nav{position:absolute;top:30px;font-family:"Poppins",sans-serif;font-size:16px;color:#222}
.nav.active{color:var(--blue);border-bottom:2px solid var(--blue);padding-bottom:2px;font-weight:500}
.btn-contact{position:absolute;left:928px;top:18px;width:155px;height:50px;border-radius:25px;background:var(--blue);color:var(--white);font-family:"Poppins",sans-serif;font-weight:600;font-size:16px;display:flex;align-items:center;justify-content:center;box-shadow:0 3px 8px rgba(0,0,0,.25)}
/* hero */
.hero-photo{position:absolute;left:0;top:88px;width:1200px;height:610px}
.hero-title{position:absolute;left:111px;top:232px;font-family:"Merriweather",serif;font-weight:900;font-size:47px;line-height:60px;color:var(--white)}
.hero-text{position:absolute;left:111px;top:360px;width:430px;font-size:15px;line-height:31px;color:var(--white)}
.btn-start{position:absolute;left:111px;top:439px;width:133px;height:46px;background:var(--blue);color:var(--white);font-family:"Merriweather",serif;font-weight:700;font-size:15px;display:flex;align-items:center;justify-content:center}
.arrow-circle{position:absolute;width:26px;height:26px;border:1.5px solid currentColor;border-radius:50%;display:flex;align-items:center;justify-content:center}
/* headings */
.sec-title{position:absolute;left:0;width:1200px;text-align:center;font-family:"Poppins",sans-serif;font-weight:600;font-size:34px;color:var(--ink)}
.sec-title span{color:var(--blue)}
.sec-title.light,.sec-title.light span{color:var(--white)}
.rule{position:absolute;width:52px;height:3px;background:var(--blue)}
.rule.light{background:var(--white)}
/* why */
.why-text{position:absolute;left:120px;top:838px;width:960px;text-align:center;font-size:15px;line-height:31px;color:#333}
.feature{position:absolute;top:930px;width:200px;text-align:center}
.feature .icon{width:60px;height:60px;margin:0 auto;border-radius:8px;background:#e3e6e9}
.feature p{margin-top:30px;font-family:"Merriweather",serif;font-weight:700;font-size:18px;color:var(--ink)}
/* about */
.about-band{position:absolute;left:0;top:1124px;width:1200px;height:582px;background:var(--blue-band)}
.about-circle{position:absolute;left:118px;top:1200px;width:430px;height:430px;border-radius:50%;border:10px solid var(--white);background:linear-gradient(160deg,#b8b5ae,#6f7378 60%,#4c5258)}
.about-title{position:absolute;left:606px;top:1204px;font-family:"Poppins",sans-serif;font-weight:600;font-size:32px;color:var(--white)}
.about-text{position:absolute;left:606px;top:1282px;width:488px;font-size:15px;line-height:31px;color:var(--white)}
.btn-read{position:absolute;left:606px;top:1571px;width:132px;height:46px;background:var(--white);color:var(--blue);font-family:"Poppins",sans-serif;font-weight:600;font-size:16px;display:flex;align-items:center;justify-content:center}
/* services */
.svc{position:absolute;top:1883px;width:311px;background:var(--white);box-shadow:0 4px 14px rgba(0,0,0,.12)}
.svc .photo{width:311px;height:242px}
.svc.plain{border-bottom:10px solid #2b2b2b;border-radius:0 0 10px 10px}
.svc.plain h3{height:82px;display:flex;align-items:center;justify-content:center;font-size:18px;color:var(--ink)}
.svc.open{background:var(--blue);padding:0 0 18px;border-radius:0 0 10px 10px}
.svc.open .body{margin:0 14px;background:var(--white);border-radius:0 0 8px 8px;padding:22px 16px 20px;text-align:center}
.svc.open h3{font-family:"Poppins",sans-serif;font-weight:600;font-size:17px;color:var(--blue)}
.svc.open p{margin-top:10px;font-size:15px;line-height:30px;color:#333}
/* testimonials */
.testi-band{position:absolute;left:0;top:2461px;width:1200px;height:560px;background:var(--blue-band)}
.testi{position:absolute;top:2613px;width:311px;height:329px;border:3px solid var(--white);border-radius:10px;padding:24px 24px}
.stars{color:var(--gold);font-size:15px;letter-spacing:2px}
.testi p{margin-top:10px;font-size:14px;line-height:26px;color:var(--white);text-align:justify}
.testi hr{border:0;border-top:1px solid rgba(255,255,255,.5);margin:30px 0 24px}
.person{display:flex;align-items:center;gap:16px}
.avatar{width:56px;height:56px;border-radius:50%;background:#d6d1c9}
.person b{display:block;font-family:"Poppins",sans-serif;font-weight:600;font-size:18px;color:var(--white)}
.person span{font-size:15px;color:var(--white)}
/* contact */
.field{position:absolute;background:var(--white);box-shadow:0 3px 14px rgba(0,0,0,.12);border-radius:4px;padding:16px 17px;font-size:14px;color:#666}
.btn-submit{position:absolute;left:531px;top:3421px;width:137px;height:50px;background:var(--blue);color:var(--white);font-family:"Poppins",sans-serif;font-weight:600;font-size:16px;display:flex;align-items:center;justify-content:center}
/* footer */
.site-footer{position:absolute;left:0;top:3541px;width:1200px;height:414px;background:var(--black);color:var(--white)}
.foot-brand{position:absolute;left:112px;top:160px;display:flex;align-items:center;gap:12px;font-family:"Poppins",sans-serif;font-weight:600;font-size:20px}
.foot-brand .dot{width:36px;height:36px;border-radius:50%;background:var(--blue)}
.foot-col{position:absolute;top:72px}
.foot-col h4{font-family:"Poppins",sans-serif;font-weight:500;font-size:21px;margin-bottom:12px}
.foot-col li{list-style:none;font-size:15px;line-height:31px;display:flex;align-items:center;gap:12px}
.contact-item{display:flex;align-items:center;gap:14px;font-size:15px;margin-bottom:24px}
.contact-item .ic{width:36px;height:36px;border-radius:50%;background:var(--blue);display:flex;align-items:center;justify-content:center}
.foot-rule{position:absolute;left:98px;top:339px;width:1004px;height:1px;background:#666}
.copy{position:absolute;left:0;top:368px;width:1200px;text-align:center;font-size:15px}
</style>
</head>
<body>

<header class="site-header">
  <div class="brand"><span class="dot"></span>Harbour Lane Removals</div>
  <a class="nav active" style="left:508px">Home</a>
  <a class="nav" style="left:597px">About Us</a>
  <a class="nav" style="left:707px">Services</a>
  <a class="nav" style="left:812px">Testimonials</a>
  <a class="btn-contact">Contact Us</a>
</header>

<section class="hero">
  <svg class="hero-photo" viewBox="0 0 1200 610" width="1200" height="610" role="img" aria-label="Two movers loading cardboard boxes into a white van on a city street">
    <defs>
      <linearGradient id="heroGrad" x1="0" y1="0" x2="1" y2="0.4">
        <stop offset="0" stop-color="#3e3d3a"/>
        <stop offset="0.55" stop-color="#6b645a"/>
        <stop offset="1" stop-color="#9a9189"/>
      </linearGradient>
    </defs>
    <path d="M0 0H1200V520C1000 580 750 612 420 600C250 594 100 570 0 518Z" fill="url(#heroGrad)"/>
    <path d="M300 598C650 622 950 590 1200 520V540C950 612 650 632 300 598Z" fill="var(--blue)"/>
    <path d="M0 518C100 570 250 594 420 600C250 600 100 580 0 540Z" fill="#fff"/>
  </svg>
  <h1 class="hero-title">Do what you do best,<br>we'll do the rest.</h1>
  <p class="hero-text">Ut enim ad minim veniam, quis nostrud exercitation ullamco laboris nisi ut aliquip ex ea commodo consequat</p>
  <a class="btn-start">Get Started</a>
  <span class="arrow-circle" style="left:54px;top:340px;color:#fff"><svg width="10" height="10" viewBox="0 0 10 10"><path d="M6.5 1.5L3 5l3.5 3.5" stroke="currentColor" stroke-width="1.5" fill="none"/></svg></span>
  <span class="arrow-circle" style="left:1140px;top:340px;color:#fff"><svg width="10" height="10" viewBox="0 0 10 10"><path d="M3.5 1.5L7 5 3.5 8.5" stroke="currentColor" stroke-width="1.5" fill="none"/></svg></span>
</section>

<section class="why">
  <h2 class="sec-title" style="top:760px">Why <span>Choose Us</span></h2>
  <div class="rule" style="left:574px;top:814px"></div>
  <p class="why-text">Lorem ipsum dolor sit amet, consectetur adipiscing elit, sed do eiusmod tempor incididunt ut labore et dolore magna aliqua. Ut enim ad minim veniam, quis nostrud exercitation ullamco laboris nisi ut aliquip ex ea commodo consequat.</p>
  <div class="feature" style="left:150px"><div class="icon" role="img" aria-label="Office building icon"></div><p>Lorem ipsum</p></div>
  <div class="feature" style="left:382px"><div class="icon" role="img" aria-label="Checklist icon"></div><p>Lorem ipsum</p></div>
  <div class="feature" style="left:614px"><div class="icon" role="img" aria-label="Team icon"></div><p>Lorem ipsum</p></div>
  <div class="feature" style="left:846px"><div class="icon" role="img" aria-label="Relocation icon"></div><p>Lorem ipsum</p></div>
</section>

<section class="about">
  <div class="about-band"></div>
  <div class="about-circle" role="img" aria-label="Two movers carrying boxes from a van"></div>
  <h2 class="about-title">About Us</h2>
  <div class="rule light" style="left:606px;top:1260px"></div>
  <p class="about-text">Sed ut perspiciatis unde omnis iste natus error sit voluptatem accusantium doloremque laudantium, totam rem aperiam, eaque ipsa quae ab illo inventore veritatis et quasi architecto beatae vitae dicta sunt explicabo. Nemo enim ipsam voluptatem quia voluptas sit aspernatur aut odit aut fugit, sed quia consequuntur magni dolores eos qui ratione voluptatem sequi nesciunt. Neque porro quisquam est, qui dolorem ipsum quia dolor sit amet, consectetur, adipisci velit, sed quia non numquam eius modi tempora incidunt ut labore et dolore magnam aliquam quaerat voluptatem.</p>
  <a class="btn-read">Read More</a>
</section>

<section class="services">
  <h2 class="sec-title" style="top:1788px">Our <span>Services</span></h2>
  <div class="rule" style="left:574px;top:1842px"></div>
  <span class="arrow-circle" style="left:49px;top:2015px;color:#888"><svg width="10" height="10" viewBox="0 0 10 10"><path d="M6.5 1.5L3 5l3.5 3.5" stroke="currentColor" stroke-width="1.5" fill="none"/></svg></span>
  <span class="arrow-circle" style="left:1128px;top:2015px;color:#333"><svg width="10" height="10" viewBox="0 0 10 10"><path d="M3.5 1.5L7 5 3.5 8.5" stroke="currentColor" stroke-width="1.5" fill="none"/></svg></span>
  <article class="svc plain" style="left:109px">
    <div class="photo" role="img" aria-label="Blue skip bin outside a house under construction" style="background:linear-gradient(180deg,#b89a78,#2c5d99 75%,#8a8170)"></div>
    <h3 style="font-family:'Poppins',sans-serif;font-weight:500">Lorem ipsum dolor amet</h3>
  </article>
  <article class="svc open" style="left:446px">
    <div class="photo" role="img" aria-label="Blue removal van being loaded" style="background:linear-gradient(160deg,#2a5fa6,#1d4478 60%,#7a7d80)"></div>
    <div class="body">
      <h3>Lorem ipsum dolor</h3>
      <p>Ut enim ad minima veniam, quis nostrum exercitationem ullam corporis suscipit laboriosam, nisi ut aliquid ex ea commodi tempora incidunt ut labore.</p>
    </div>
  </article>
  <article class="svc plain" style="left:782px">
    <div class="photo" role="img" aria-label="Movers in blue uniforms handling boxes in a home" style="background:linear-gradient(160deg,#d8d2c6,#2f4f86 55%,#c7a27a)"></div>
    <h3 style="font-family:'Merriweather',serif;font-weight:700">Brokerage</h3>
  </article>
</section>

<section class="testimonials">
  <div class="testi-band"></div>
  <h2 class="sec-title light" style="top:2508px">Client&nbsp; <span>Testimonials</span></h2>
  <div class="rule light" style="left:574px;top:2570px"></div>
  <span class="arrow-circle" style="left:43px;top:2775px;width:38px;height:38px;color:#fff"><svg width="12" height="12" viewBox="0 0 10 10"><path d="M6.5 1.5L3 5l3.5 3.5" stroke="currentColor" stroke-width="1.5" fill="none"/></svg></span>
  <span class="arrow-circle" style="left:1132px;top:2775px;width:38px;height:38px;color:var(--blue);background:#fff;border-color:#fff"><svg width="12" height="12" viewBox="0 0 10 10"><path d="M3.5 1.5L7 5 3.5 8.5" stroke="currentColor" stroke-width="1.5" fill="none"/></svg></span>
  <article class="testi" style="left:111px">
    <div class="stars">★★★★★</div>
    <p>Lorem ipsum dolor sit amet, consectetur adipiscing elit, sed do eiusmod tempor incididunt ut labore et dolore magna aliqua ut enim ad minim veniam, quis nostrud exercitation ullamco.</p>
    <hr>
    <div class="person"><div class="avatar" role="img" aria-label="Client portrait"></div><div><b>Jordan Reyes</b><span>Harbour Bay, Coastline</span></div></div>
  </article>
  <article class="testi" style="left:447px">
    <div class="stars">★★★★★</div>
    <p>Lorem ipsum dolor sit amet, consectetur adipiscing elit, sed do eiusmod tempor incididunt ut labore et dolore magna aliqua ut enim ad minim veniam, quis nostrud exercitation ullamco.</p>
    <hr>
    <div class="person"><div class="avatar" role="img" aria-label="Client portrait"></div><div><b>Jordan Reyes</b><span>Harbour Bay, Coastline</span></div></div>
  </article>
  <article class="testi" style="left:783px">
    <div class="stars">★★★★★</div>
    <p>Lorem ipsum dolor sit amet, consectetur adipiscing elit, sed do eiusmod tempor incididunt ut labore et dolore magna aliqua ut enim ad minim veniam, quis nostrud exercitation ullamco.</p>
    <hr>
    <div class="person"><div class="avatar" role="img" aria-label="Client portrait"></div><div><b>Jordan Reyes</b><span>Harbour Bay, Coastline</span></div></div>
  </article>
</section>

<section class="contact">
  <h2 class="sec-title" style="top:3078px">Contact <span>Us</span></h2>
  <div class="rule" style="left:574px;top:3132px"></div>
  <div class="field" style="left:181px;top:3186px;width:412px;height:49px">Name</div>
  <div class="field" style="left:606px;top:3186px;width:412px;height:49px">Email</div>
  <div class="field" style="left:181px;top:3249px;width:412px;height:49px">Phone Number</div>
  <div class="field" style="left:606px;top:3249px;width:412px;height:49px">Subject</div>
  <div class="field" style="left:181px;top:3311px;width:837px;height:86px">Message</div>
  <a class="btn-submit">Submit</a>
</section>

<footer class="site-footer">
  <div class="foot-brand"><span class="dot"></span>Harbour Lane Removals</div>
  <div class="foot-col" style="left:402px">
    <h4>Quick Links</h4>
    <ul>
      <li>➔ Home</li><li>➔ About Us</li><li>➔ Services</li><li>➔ Solutions</li><li>➔ Blog</li><li>➔ Contact Us</li>
    </ul>
  </div>
  <div class="foot-col" style="left:626px">
    <h4>Other Links</h4>
    <ul>
      <li>➔ FAQ</li><li>➔ Tems of Use</li><li>➔ Privacy Policy</li><li>➔ Support Links</li><li>➔ Conditions</li>
    </ul>
  </div>
  <div class="foot-col" style="left:847px">
    <h4 style="margin-bottom:20px">Contact Us</h4>
    <div class="contact-item"><span class="ic"><svg width="14" height="16" viewBox="0 0 14 16"><path d="M7 1a5 5 0 0 0-5 5c0 4 5 9 5 9s5-5 5-9a5 5 0 0 0-5-5z" fill="#fff"/><circle cx="7" cy="6" r="2" fill="var(--blue)"/></svg></span>Harbour Lane Removals, Harbour Bay.</div>
    <div class="contact-item"><span class="ic"><svg width="16" height="12" viewBox="0 0 16 12"><rect x="1" y="1" width="14" height="10" rx="1" fill="#fff"/><path d="M1 2l7 5 7-5" stroke="var(--blue)" stroke-width="1.3" fill="none"/></svg></span>hello@harbourlaneremovals.com</div>
    <div class="contact-item"><span class="ic"><svg width="14" height="14" viewBox="0 0 14 14"><path d="M3 1l2.5 3-1.5 1.5a8 8 0 0 0 4.5 4.5L10 8.5l3 2.5-1.5 2C6 13 1 8 1 2.5z" fill="#fff"/></svg></span>+1 555 0142 0199</div>
  </div>
  <div class="foot-rule"></div>
  <p class="copy">Copyrights@2024.Harbour Lane Removals.All Rights Reserved</p>
</footer>

</body>
</html>
```